Modern Business Card

Modern professional business card with more than just logo and demographic info. Something memorable.

We are a trendy/modern chiropractic group with an emphasis on neurology, hence the minimalist-type brain logo. We want to convey that modern and technical aspect with professionalism and the elite nature of our practice environment.

```html
<!DOCTYPE html>
<html lang="en">
<head>
<meta charset="utf-8">
<title>Kinetic Chiropractic – Business Card</title>
<link rel="stylesheet" href="https://fonts.googleapis.com/css2?family=Titillium+Web:wght@700&family=Source+Serif+4:wght@400;600&display=swap">
<style>
  :root {
    --backdrop: #3a3a3a;
    --card-black: #1e1e1f;
    --card-dark: #262627;
    --brand-blue: #4a6aab;
    --accent-brown: #5b4848;
    --ink-white: #ffffff;
    --ink-soft: #e8ecf5;
    --emboss: #6a6a6c;
  }
  * { box-sizing: border-box; margin: 0; padding: 0; }
  html, body { width: 799px; height: 1200px; overflow: hidden; }
  body { background: var(--backdrop); position: relative; }

  .card {
    position: absolute;
    left: 80px;
    width: 640px;
    height: 366px;
    border-radius: 4px;
    overflow: hidden;
    box-shadow: 0 14px 30px rgba(0,0,0,.45);
  }
  .card--front { top: 117px; background: var(--card-black); }
  .card--back  { top: 717px; background: var(--brand-blue); }

  .front-mark {
    position: absolute; inset: 0;
    display: flex; align-items: center; justify-content: center; gap: 14px;
    font-family: "Source Serif 4", serif;
    font-weight: 600;
    font-size: 34px;
    letter-spacing: 3px;
    text-transform: uppercase;
    color: var(--emboss);
  }
  .front-mark__square { width: 22px; height: 22px; background: var(--emboss); }

  .back-curve { position: absolute; inset: 0; }

  .holder { position: absolute; left: 36px; top: 30px; color: var(--ink-white); }
  .holder__name { font-family: "Titillium Web", sans-serif; font-weight: 700; font-size: 22px; line-height: 1.1; }
  .holder__title { font-family: "Source Serif 4", serif; font-size: 14px; color: var(--ink-soft); }

  .contact { position: absolute; left: 36px; top: 176px; list-style: none; color: var(--ink-white);
    font-family: "Source Serif 4", serif; font-size: 14px; line-height: 22px; }
  .contact__row { display: flex; align-items: center; gap: 8px; }
  .contact__icon { width: 13px; height: 13px; fill: var(--ink-white); flex: none; }
  .contact__address { margin-top: 4px; font-size: 15px; line-height: 20px; }

  .brand {
    position: absolute; right: 34px; top: 170px; width: 250px;
    display: flex; flex-direction: column; align-items: center; gap: 14px;
    font-family: "Source Serif 4", serif; font-weight: 600;
    color: var(--ink-white); text-transform: uppercase; text-align: center;
    font-size: 28px; line-height: 1.05; letter-spacing: 1px;
  }
  .brand__square { width: 56px; height: 56px; background: var(--brand-blue); }
</style>
</head>
<body>

<section class="card card--front" aria-label="Card front">
  <div class="front-mark"><span class="front-mark__square"></span><span>Kinetic Chiropractic</span></div>
</section>

<section class="card card--back" aria-label="Card back">
  <svg class="back-curve" width="640" height="366" viewBox="0 0 640 366" aria-hidden="true">
    <path d="M 462 0 Q 360 170 366 366" fill="none" stroke="var(--accent-brown)" stroke-width="10"/>
    <path d="M 472 0 Q 372 170 378 366 L 640 366 L 640 0 Z" fill="var(--card-dark)"/>
  </svg>

  <div class="holder">
    <p class="holder__name">Alex Morgan Reed</p>
    <p class="holder__title">Managing Director</p>
  </div>

  <ul class="contact">
    <li class="contact__row">
      <svg class="contact__icon" viewBox="0 0 16 16"><path d="M3 1h3l1.5 3.5-2 1.5a9 9 0 0 0 4.5 4.5l1.5-2L15 10v3a2 2 0 0 1-2 2A12 12 0 0 1 1 3a2 2 0 0 1 2-2z"/></svg>
      <span>555-210-4477</span>
    </li>
    <li class="contact__row">
      <svg class="contact__icon" viewBox="0 0 16 16"><path d="M1 3h14v10H1z M1 3l7 6 7-6" stroke="#fff" stroke-width="1.2" fill="none"/></svg>
      <span>alex@kineticchiropractic.com</span>
    </li>
    <li class="contact__row">
      <svg class="contact__icon" viewBox="0 0 16 16"><circle cx="8" cy="8" r="7"/><path d="M1 8h14M8 1c-3 4-3 10 0 14M8 1c3 4 3 10 0 14" stroke="#4a6aab" stroke-width="1" fill="none"/></svg>
      <span>www.kineticchiropractic.com</span>
    </li>
    <li class="contact__address">48 Sample Ave., Some City,<br>Some Town, ST 100234</li>
  </ul>

  <div class="brand">
    <span class="brand__square"></span>
    <span>Kinetic<br>Chiropractic</span>
  </div>
</section>

</body>
</html>
```